Beacon Advisory Website

I currently have a website www.beaconadvisoryinc.com. We are a IT Consulting Company. Our website will pretty much tell out our services. I am looking to enhance my website and make it look more professional. Looking for very classy and Contemporary look and design for my website.

It Company

```html
<!DOCTYPE html>
<html lang="en">
<head>
<meta charset="utf-8">
<title>Beacon Advisory</title>
<link href="https://fonts.googleapis.com/css2?family=Open+Sans:wght@300;400;600;700&display=swap" rel="stylesheet">
<style>
:root{
  --brand:#1a5fa8;
  --brand-dark:#0d3e73;
  --ink:#333a40;
  --muted:#6f767c;
  --line:#2b3238;
  --tile:#222426;
  --tile-active:#1b56a0;
  --soft:#f3f4f5;
  --footer:#3a3b3c;
  --white:#ffffff;
}
*{box-sizing:border-box;margin:0;padding:0}
html,body{width:742px;height:1200px;overflow:hidden;background:var(--white)}
body{position:relative;font-family:"Open Sans",Arial,sans-serif;color:var(--ink)}
.abs{position:absolute}

/* header */
.site-header{left:0;top:0;width:742px;height:65px;background:var(--white);border-top:2px solid #2a8fd6}
.brand{left:62px;top:20px;display:flex;align-items:center;gap:7px}
.brand-dot{width:22px;height:22px;border-radius:50%;background:var(--brand)}
.brand-name{font-size:13px;font-weight:700;color:var(--brand-dark);letter-spacing:.3px}
.main-nav{top:29px;font-size:7px;color:#222;letter-spacing:.2px}
.main-nav span{position:absolute;white-space:nowrap}
.main-nav .active{color:var(--brand)}
.search{left:673px;top:30px}

/* hero */
.hero{left:0;top:65px;width:742px;height:310px;
  background:radial-gradient(circle at 62% 35%,#3f86c6 0%,#1f5c98 30%,#0f3561 65%,#0a2444 100%)}
.hero-title{left:62px;top:185px;font-size:32px;font-weight:700;color:var(--white);letter-spacing:.5px}
.hero-sub{left:62px;top:230px;font-size:16px;font-weight:300;color:var(--white)}
.hero-arrow{top:204px}

/* sections */
.section-title{left:0;width:742px;text-align:center;font-size:16px;font-weight:400;color:var(--ink)}
.section-title em{font-style:normal;color:var(--brand)}
.rule{left:349px;width:44px;height:1px;background:var(--line)}
.intro{left:70px;top:440px;width:602px;text-align:center;font-size:6.4px;line-height:14.6px;color:var(--muted)}

.services{left:0;top:508px;width:742px;height:275px;
  background:linear-gradient(180deg,#2a8ed3 0%,#1a76c0 40%,#1b7bc6 75%,#4ea6df 100%)}
.services .section-title{color:var(--white)}
.services-lead{left:0;top:569px;width:742px;text-align:center;font-size:7px;color:var(--white)}
.service{top:607px;width:150px;text-align:center;color:var(--white)}
.service-tile{width:78px;height:77px;margin:0 auto;background:var(--tile);display:flex;align-items:center;justify-content:center;box-shadow:0 1px 3px rgba(0,0,0,.3)}
.service-tile.is-active{background:var(--tile-active)}
.service h3{margin-top:10px;font-size:9.5px;font-weight:400}
.service p{margin-top:4px;font-size:6.6px;line-height:13.6px}

.solutions-lead{left:0;top:845px;width:742px;text-align:center;font-size:7px;color:var(--muted)}
.solution{top:877px;width:191px}
.solution-media{width:191px;height:105px;border:2px solid #fff;box-shadow:0 2px 5px rgba(0,0,0,.35)}
.solution h3{margin-top:12px;text-align:center;font-size:11px;font-weight:400;color:var(--ink)}
.solution h3.is-active{color:var(--brand)}

/* testimonial */
.testimonial{left:0;top:1034px;width:742px;height:113px;background:var(--soft)}
.avatar{left:69px;top:1051px;width:74px;height:74px;border-radius:50%;border:3px solid #fff;
  background:radial-gradient(circle at 50% 40%,#e5e2df 0%,#c9c6c2 60%,#a9b3bd 100%)}
.quote{left:175px;top:1059px;width:490px;font-size:6.4px;line-height:14.7px;color:#8a8f94}
.qmark{font-size:16px;color:#c8cbce;font-family:Georgia,serif}
.author{left:175px;top:1114px;font-size:6.4px;color:var(--brand)}
.role{left:175px;top:1127px;font-size:7px;color:#222}

/* footer */
.site-footer{left:0;top:1147px;width:742px;height:53px;background:var(--footer)}
.footer-nav{left:62px;top:1158px;font-size:6.6px;color:#e6e6e6;word-spacing:2px}
.copyright{left:62px;top:1178px;font-size:6.6px;color:#e6e6e6}
.social{top:1165px;width:18px;height:18px;border-radius:50%;background:#5f6062;border:1px solid #777}
</style>
</head>
<body>

<header class="abs site-header">
  <div class="abs brand"><span class="brand-dot"></span><span class="brand-name">Beacon Advisory</span></div>
  <nav class="abs main-nav" style="left:0;width:742px">
    <span class="active" style="left:322px">HOME</span>
    <span style="left:360px">COMPANY</span>
    <span style="left:411px">SERVICES</span>
    <span style="left:458px">SOLUTIONS</span>
    <span style="left:514px">RESOURCES</span>
    <span style="left:570px">CAREER</span>
    <span style="left:614px">CONTACT US</span>
  </nav>
  <svg class="abs search" width="9" height="9" viewBox="0 0 10 10"><circle cx="4" cy="4" r="3" fill="none" stroke="#1a5fa8" stroke-width="1.6"/><line x1="6.3" y1="6.3" x2="9.2" y2="9.2" stroke="#1a5fa8" stroke-width="1.8"/></svg>
</header>

<section class="abs hero" role="img" aria-label="Hand holding glowing connected network spheres on a blue background"></section>
<h1 class="abs hero-title">BEACON ADVISORY</h1>
<p class="abs hero-sub">AT VERO EOS ET ACCUSAMUS AT</p>
<svg class="abs hero-arrow" style="left:27px" width="10" height="34" viewBox="0 0 10 34"><polyline points="9,1 1,17 9,33" fill="none" stroke="rgba(255,255,255,.6)" stroke-width="1"/></svg>
<svg class="abs hero-arrow" style="left:705px" width="10" height="34" viewBox="0 0 10 34"><polyline points="1,1 9,17 1,33" fill="none" stroke="rgba(255,255,255,.6)" stroke-width="1"/></svg>

<h2 class="abs section-title" style="top:393px"><em>Welcome To</em> Our Company</h2>
<div class="abs rule" style="top:426px"></div>
<p class="abs intro">Today's IT market is a dynamic, fast-paced industry, with ever-increasing demands. Meeting these demands for over 25 years, Beacon Advisory maintains a global presence, aggressively recruiting expertly qualified IT and Management Professionals from around the world and cultivating key partnerships with corporations to understand their business models end-to-end, with a goal of delivering exceptional client service and ensuring a consistent delivery of the talent needed to drive results.</p>

<section class="abs services" role="img" aria-label="Blurred blue abstract light background"></section>
<h2 class="abs section-title" style="top:519px;color:#fff">Our Services</h2>
<p class="abs services-lead">Beacon Advisory Training programs are perfect for individuals to enhance their careers. Our hands-on practical and interactive programs</p>

<article class="abs service" style="left:53px">
  <div class="service-tile is-active">
    <svg width="30" height="28" viewBox="0 0 30 28"><rect x="1.5" y="1.5" width="27" height="18" rx="2" fill="none" stroke="#fff" stroke-width="3"/><rect x="12" y="20" width="6" height="4" fill="#fff"/><rect x="8" y="24" width="14" height="2.5" fill="#fff"/></svg>
  </div>
  <h3>Technology</h3>
  <p>Beacon Advisory provides training choices in multiple formats and delivery methods, offering top-quality training custom-tailored</p>
</article>
<article class="abs service" style="left:215px">
  <div class="service-tile">
    <svg width="30" height="26" viewBox="0 0 30 26"><rect x="10" y="1.5" width="10" height="5" rx="1" fill="none" stroke="#fff" stroke-width="2.4"/><rect x="1" y="6" width="28" height="19" rx="2" fill="#fff"/><rect x="1" y="13" width="28" height="2" fill="#222426"/><rect x="13" y="11.5" width="4" height="5" fill="#fff"/></svg>
  </div>
  <h3>Business</h3>
  <p>Beacon Advisory provides training choices in multiple formats and delivery methods, offering top-quality training custom-tailored</p>
</article>
<article class="abs service" style="left:376px">
  <div class="service-tile">
    <svg width="30" height="28" viewBox="0 0 30 28"><path d="M17 4H5a3 3 0 0 0-3 3v16a3 3 0 0 0 3 3h16a3 3 0 0 0 3-3V13" fill="none" stroke="#fff" stroke-width="2.6"/><path d="M24 2l4 4-12 12-5 1 1-5z" fill="#fff"/></svg>
  </div>
  <h3>Application</h3>
  <p>Beacon Advisory provides training choices in multiple formats and delivery methods, offering top-quality training custom-tailored</p>
</article>
<article class="abs service" style="left:538px">
  <div class="service-tile">
    <svg width="30" height="30" viewBox="0 0 30 30" fill="none" stroke="#fff" stroke-width="1.6"><polygon points="15,2 27,9 27,21 15,28 3,21 3,9"/><polygon points="15,8 21,12 21,18 15,22 9,18 9,12"/><path d="M15 2V8M27 9L21 12M27 21L21 18M15 28V22M3 21L9 18M3 9L9 12"/></svg>
  </div>
  <h3>Developement</h3>
  <p>Beacon Advisory provides training choices in multiple formats and delivery methods, offering top-quality training custom-tailored</p>
</article>

<h2 class="abs section-title" style="top:801px"><em>Our</em> Solution</h2>
<div class="abs rule" style="top:830px"></div>
<p class="abs solutions-lead">Our proven implementation and audit models allow for capturing requirements while expiditing the process.</p>

<article class="abs solution" style="left:62px">
  <div class="solution-media" role="img" aria-label="Business person touching a digital dashboard of charts" style="background:linear-gradient(135deg,#6e8fae 0%,#a9bfd3 45%,#d9e2ea 100%)"></div>
  <h3 class="is-active">Dashboards</h3>
</article>
<article class="abs solution" style="left:275px">
  <div class="solution-media" role="img" aria-label="Illustration of data warehouse servers over a world map" style="background:linear-gradient(135deg,#1f73c6 0%,#2a86d6 55%,#1b66b3 100%)"></div>
  <h3>Data Warehousing</h3>
</article>
<article class="abs solution" style="left:490px">
  <div class="solution-media" role="img" aria-label="Business person arranging gears with people icons" style="background:linear-gradient(135deg,#e4e7ea 0%,#b5bcc4 50%,#3f4650 100%)"></div>
  <h3>Business Process Management</h3>
</article>

<section class="abs testimonial"></section>
<div class="abs avatar" role="img" aria-label="Portrait of the quoted marketing executive"></div>
<span class="abs qmark" style="left:160px;top:1046px">&ldquo;</span>
<p class="abs quote">Lorem Ipsum es simplemente el texto de relleno de las imprentas y archivos de texto. Lorem Ipsum ha sido el texto de relleno estándar de las industrias desde el año 1500, cuando un impresor (N. del T. persona que se dedica a la imprenta) desconocido usó una galería On the other hand, we denounce&nbsp; moment, so blinded by desire, that they cannot foresee...</p>
<span class="abs qmark" style="left:647px;top:1082px">&rdquo;</span>
<span class="abs author">MARCUS HALE</span>
<span class="abs role">Marketing Executive</span>

<footer class="abs site-footer"></footer>
<p class="abs footer-nav">HOME&nbsp; / &nbsp;COMPANY&nbsp; / &nbsp;SERVICES&nbsp; / &nbsp;SOLUTIONS&nbsp; / &nbsp;RESOURCES&nbsp; / &nbsp;CAREER&nbsp; / &nbsp;CONTACT US</p>
<p class="abs copyright">2016 © Copy right .Beacon Advisory all right reserved</p>
<span class="abs social" style="left:600px"></span>
<span class="abs social" style="left:621px"></span>
<span class="abs social" style="left:641px"></span>
<span class="abs social" style="left:662px"></span>

</body>
</html>
```